Bluecrest Learning Corps by graduating students from college in two years

Based on the logo design, create stationary and business cards for
Dr. Venrel T Oskamp, CEO, (703) 482-1736
and Marisa Deltoft, Respresentative, (301) 647-2208
Address: 4719 Pellham Court, Harlow Ridge, VA 22471
Incorporate elelments of the logo

Target Market(s)

USA

Font styles to use
Other font styles liked:
• match with the logo type style

```html
<!DOCTYPE html>
<html lang="en">
<head>
<meta charset="utf-8">
<title>Bluecrest Learning Corps – Stationery Set</title>
<link rel="stylesheet" href="https://fonts.googleapis.com/css2?family=Roboto+Slab:wght@600&family=Tinos&family=Open+Sans:wght@400;600&family=Dancing+Script:wght@600&display=swap">
<style>
  :root{
    --gold:#f8c630;
    --navy:#1f2a5e;
    --paper:#ffffff;
    --bg-top:#dcdddf;
    --bg-bottom:#cfd0d2;
    --ink:#333;
    --rule:#555;
  }
  *{box-sizing:border-box;margin:0;padding:0}
  html,body{width:1039px;height:1200px;overflow:hidden}
  body{position:relative;background:linear-gradient(var(--bg-top) 0 826px,var(--bg-bottom) 826px);font-family:"Tinos",serif;color:var(--ink)}
  .piece{position:absolute;background:var(--paper);box-shadow:0 2px 5px rgba(0,0,0,.22)}
  .rounded{border-radius:10px}

  /* brand mark: plain circle + name */
  .mark{display:flex;flex-direction:column;align-items:center;gap:3px;text-align:center;font-family:"Tinos",serif;color:var(--navy);line-height:1.1}
  .mark .dot{border-radius:50%;background:var(--navy)}
  .mark.on-gold{color:var(--navy)}

  .divider{position:absolute;width:1px;background:var(--gold)}
  .name{font-family:"Roboto Slab",serif;font-weight:600;color:var(--gold)}
  .ico{width:6px;height:6px;fill:var(--gold);vertical-align:-0.5px;margin-right:3px}

  /* business card front */
  .card-ceo{left:60px;top:79px;width:271px;height:155px}
  .card-ceo .mark{position:absolute;left:28px;top:48px;width:72px;font-size:8px}
  .card-ceo .mark .dot{width:20px;height:20px}
  .card-ceo .divider{left:111px;top:46px;height:64px}
  .card-ceo .info{position:absolute;left:124px;top:45px;font-size:7.5px;line-height:10.5px}
  .card-ceo .name{font-size:12px;line-height:14px}
  .gap{height:6px}

  /* business card back */
  .card-back{left:60px;top:273px;width:271px;height:156px;background:var(--gold);display:flex;align-items:center;justify-content:center}
  .card-back .mark{font-size:12px;width:140px}
  .card-back .mark .dot{width:34px;height:34px}

  /* letterhead */
  .letterhead{left:347px;top:78px;width:250px;height:354px;font-family:"Open Sans",sans-serif}
  .letterhead .mark{position:absolute;left:18px;top:18px;width:55px;font-size:6px}
  .letterhead .mark .dot{width:16px;height:16px}
  .letterhead .contact{position:absolute;left:170px;top:20px;font-family:"Tinos",serif;font-size:4.8px;line-height:6.4px;border-left:1px solid var(--gold);padding-left:5px}
  .letterhead .ico{width:4px;height:4px}
  .recipient{position:absolute;left:24px;top:82px;font-size:4.6px;line-height:6px}
  .recipient strong{font-weight:400;font-size:5px}
  .letter-body{position:absolute;left:24px;top:125px;width:203px;font-size:3.7px;line-height:6.1px;text-align:justify;color:#444}
  .letter-body p{margin-bottom:5.8px}
  .signoff{position:absolute;left:24px;top:262px;font-size:4.4px;line-height:6px;color:#444}
  .signoff .signer{margin-top:14px}
  .letter-foot{position:absolute;left:24px;bottom:9px;font-family:"Tinos",serif;font-size:4.2px;color:var(--ink)}
  .foot-band{position:absolute;right:0;bottom:8px;width:114px;height:5px}

  /* envelope back */
  .envelope-back{left:618px;top:78px;width:357px;height:157px}
  .envelope-back .flap{position:absolute;left:0;top:0;width:357px;height:58px}
  .envelope-back .mark{position:absolute;left:139px;top:6px;width:80px;font-size:6.5px}
  .envelope-back .mark .dot{width:18px;height:18px}

  /* envelope front */
  .envelope-front{left:618px;top:277px;width:357px;height:154px}
  .envelope-front .mark{position:absolute;left:14px;top:14px;width:58px;font-size:6px}
  .envelope-front .mark .dot{width:16px;height:16px}
  .envelope-front .addr{position:absolute;left:17px;top:52px;font-size:5.6px;line-height:7.6px}

  /* representative card */
  .card-rep{left:60px;top:491px;width:274px;height:99px}
  .card-rep .mark{position:absolute;left:58px;top:30px;width:66px;font-size:7px}
  .card-rep .mark .dot{width:18px;height:18px}
  .card-rep .divider{left:130px;top:20px;height:62px}
  .card-rep .info{position:absolute;left:141px;top:18px;font-size:6.2px;line-height:9px}
  .card-rep .name{font-size:11px;line-height:13px}

  /* compliments slip */
  .comp-slip{left:61px;top:637px;width:273px;height:129px}
  .comp-slip .mark{position:absolute;left:12px;top:13px;width:62px;font-size:6px}
  .comp-slip .mark .dot{width:16px;height:16px}
  .comp-slip .greeting{position:absolute;right:14px;top:10px;font-family:"Dancing Script",cursive;font-size:14px;color:var(--gold)}
  .comp-slip .greeting span{color:var(--navy)}
  .comp-slip .addr{position:absolute;left:12px;top:89px;font-size:5px;line-height:7px}
  .comp-slip .ico{width:4.5px;height:4.5px}

  /* notebook cover */
  .notebook{left:365px;top:492px;width:191px;height:271px;background:var(--gold);box-shadow:3px 3px 6px rgba(0,0,0,.3);display:flex;align-items:center;justify-content:center}
  .notebook .mark{font-size:13px;width:140px}
  .notebook .mark .dot{width:40px;height:40px}
  .spiral{position:absolute;left:358px;top:498px;width:22px;height:262px}

  /* notebook spread */
  .notebook-open{left:590px;top:492px;width:386px;height:272px;display:flex;background:#f7f7f7}
  .notebook-open .page{position:relative;flex:1;height:100%}
  .notebook-open .page+.page{border-left:4px solid #ddd}
  .page .mark{position:absolute;left:8px;top:6px;width:50px;font-size:5px}
  .page .mark .dot{width:15px;height:15px}
  .page .date{position:absolute;right:8px;top:19px;font-family:"Open Sans",sans-serif;font-size:6px;color:#555}
  .page .lines{position:absolute;left:9px;right:9px;top:42px;height:209px;background:repeating-linear-gradient(to bottom,transparent 0 10px,var(--rule) 10px 11px)}
  .rings{position:absolute;left:777px;top:497px;width:14px;height:262px}

  /* brochure, flat */
  .brochure{left:60px;top:880px;width:400px;height:272px;display:flex}
  .brochure .panel{position:relative;flex:1;height:100%}
  .brochure .back{background:var(--paper)}
  .brochure .front{background:var(--gold)}
  .brochure .back .mark{position:absolute;left:35px;top:55px;width:130px;font-size:12px}
  .brochure .back .mark .dot{width:46px;height:46px}
  .brochure .front .mark{position:absolute;left:40px;top:50px;width:120px;font-size:11px}
  .brochure .front .mark .dot{width:36px;height:36px}
  .brochure .back .addr{position:absolute;left:0;right:0;bottom:18px;text-align:center;font-size:5px;line-height:7px}
  .brochure .back .ico{width:4.5px;height:4.5px}
  .brochure .front .credit{position:absolute;left:0;right:0;bottom:20px;text-align:center;font-size:4.8px;color:var(--navy)}

  /* presentation folder, flat */
  .folder{left:560px;top:880px;width:416px;height:272px;display:flex;background:var(--paper)}
  .folder .panel{position:relative;flex:1;height:100%}
  .folder .panel+.panel{border-left:1px solid #e2e2e2}
  .pocket{position:absolute;left:0;right:0;bottom:0;height:92px}
  .pocket-gold{background:var(--gold);display:flex;align-items:center;justify-content:center}
  .pocket-gold .mark{width:90px;font-size:7px}
  .pocket-gold .mark .dot{width:20px;height:20px}
  .pocket-navy{background:var(--navy);clip-path:polygon(0 18%,100% 0,100% 100%,0 100%)}
  .folder .mini-card{position:absolute;left:52px;top:162px;width:104px;height:44px;background:var(--paper);box-shadow:0 1px 3px rgba(0,0,0,.35)}
  .mini-card .dot{position:absolute;left:10px;top:15px;width:12px;height:12px;border-radius:50%;background:var(--navy)}
  .mini-card .info{position:absolute;left:34px;top:7px;font-size:3.6px;line-height:5px;border-left:.6px solid var(--gold);padding-left:4px}
  .mini-card .name{font-size:5px;line-height:6px}
</style>
</head>
<body>

<!-- CEO business card front -->
<section class="piece rounded card-ceo" aria-label="CEO business card">
  <div class="mark"><span class="dot"></span>Bluecrest Learning Corps</div>
  <span class="divider"></span>
  <div class="info">
    <div class="name">Dr. Venrel T Oskamp</div>
    <div>CEO</div>
    <div class="gap"></div>
    <div>4719 Pellham Court,</div>
    <div>Harlow Ridge, VA 22471</div>
    <div class="gap"></div>
    <div><svg class="ico" viewBox="0 0 10 10"><path d="M1 3c0-1 1-2 2-2h4c1 0 2 1 2 2v1H7V3H3v1H1zM2 5h6l1 4H1z"/></svg>(703) 482-1736</div>
  </div>
</section>

<!-- Business card back -->
<section class="piece rounded card-back" aria-label="Business card back">
  <div class="mark on-gold"><span class="dot"></span>Bluecrest Learning Corps</div>
</section>

<!-- Letterhead -->
<section class="piece letterhead" aria-label="Letterhead">
  <div class="mark"><span class="dot"></span>Bluecrest Learning Corps</div>
  <div class="contact">
    <div>4719 Pellham Court,</div>
    <div>Harlow Ridge, VA 22471</div>
    <div style="height:3px"></div>
    <div><svg class="ico" viewBox="0 0 10 10"><path d="M1 3c0-1 1-2 2-2h4c1 0 2 1 2 2v1H7V3H3v1H1zM2 5h6l1 4H1z"/></svg>(703) 482-1736</div>
    <div><svg class="ico" viewBox="0 0 10 10"><path d="M1 3c0-1 1-2 2-2h4c1 0 2 1 2 2v1H7V3H3v1H1zM2 5h6l1 4H1z"/></svg>(301) 647-2208</div>
  </div>
  <div class="recipient">
    <strong>CORINNE VALE</strong><br>Chief Executive Officer<br>City/State, Zip Code
  </div>
  <div class="letter-body">
    <p>Thank you for your interest in our accelerated programs. Our advisors guide each student through a focused plan that pairs core science and math courses with hands-on lab work, so graduates finish a full degree in two years and step directly into skilled roles.</p>
    <p>This letter confirms your enrollment review is complete. Your schedule, tutor contacts and course list are attached for your records. Please keep them handy during orientation week and reach out to our office with any questions before classes begin.</p>
    <p>We look forward to welcoming you to campus and supporting your path into the technical workforce with clear milestones and steady mentoring.</p>
  </div>
  <div class="signoff">Sincerely,<div class="signer">Anselm Reyko</div></div>
  <div class="letter-foot">Dr. Venrel T Oskamp, CEO / Marisa Deltoft, Respresentative</div>
  <svg class="foot-band" viewBox="0 0 114 5" preserveAspectRatio="none">
    <polygon points="0,5 4,0 9,0 5,5" fill="var(--gold)"/>
    <polygon points="8,5 12,0 21,0 17,5" fill="var(--navy)"/>
    <polygon points="20,5 24,0 114,0 114,5" fill="var(--gold)"/>
  </svg>
</section>

<!-- Envelope back -->
<section class="piece envelope-back" aria-label="Envelope back">
  <svg class="flap" viewBox="0 0 357 58" preserveAspectRatio="none">
    <path d="M0 0H357L345 42Q340 57 325 57H32Q17 57 12 42Z" fill="var(--gold)"/>
  </svg>
  <div class="mark on-gold"><span class="dot"></span>Bluecrest Learning Corps</div>
</section>

<!-- Envelope front -->
<section class="piece envelope-front" aria-label="Envelope front">
  <div class="mark"><span class="dot"></span>Bluecrest Learning Corps</div>
  <div class="addr">4719 Pellham Court,<br>Harlow Ridge, VA 22471</div>
</section>

<!-- Representative business card -->
<section class="piece card-rep" aria-label="Representative business card">
  <div class="mark"><span class="dot"></span>Bluecrest Learning Corps</div>
  <span class="divider"></span>
  <div class="info">
    <div class="name">Marisa Deltoft</div>
    <div>Respresentative</div>
    <div style="height:5px"></div>
    <div>4719 Pellham Court,</div>
    <div>Harlow Ridge, VA 22471</div>
    <div style="height:5px"></div>
    <div><svg class="ico" viewBox="0 0 10 10"><path d="M1 3c0-1 1-2 2-2h4c1 0 2 1 2 2v1H7V3H3v1H1zM2 5h6l1 4H1z"/></svg>(301) 647-2208</div>
  </div>
</section>

<!-- Compliments slip -->
<section class="piece comp-slip" aria-label="Compliments slip">
  <div class="mark"><span class="dot"></span>Bluecrest Learning Corps</div>
  <div class="greeting"><span>with</span> compliments</div>
  <div class="addr">
    4719 Pellham Court,<br>Harlow Ridge, VA 22471<br>
    <div style="height:3px"></div>
    <svg class="ico" viewBox="0 0 10 10"><path d="M1 3c0-1 1-2 2-2h4c1 0 2 1 2 2v1H7V3H3v1H1zM2 5h6l1 4H1z"/></svg>(703) 482-1736<br>
    <svg class="ico" viewBox="0 0 10 10"><path d="M1 3c0-1 1-2 2-2h4c1 0 2 1 2 2v1H7V3H3v1H1zM2 5h6l1 4H1z"/></svg>(301) 647-2208
  </div>
</section>

<!-- Notebook cover -->
<section class="piece notebook" aria-label="Notebook cover">
  <div class="mark on-gold"><span class="dot"></span>Bluecrest Learning Corps</div>
</section>
<svg class="spiral" viewBox="0 0 22 262" aria-hidden="true">
  <g stroke="#111" stroke-width="2.4" stroke-linecap="round">
    <line x1="2" y1="4" x2="20" y2="4"/><line x1="2" y1="19.7" x2="20" y2="19.7"/><line x1="2" y1="35.4" x2="20" y2="35.4"/><line x1="2" y1="51.1" x2="20" y2="51.1"/><line x1="2" y1="66.8" x2="20" y2="66.8"/><line x1="2" y1="82.5" x2="20" y2="82.5"/><line x1="2" y1="98.2" x2="20" y2="98.2"/><line x1="2" y1="113.9" x2="20" y2="113.9"/><line x1="2" y1="129.6" x2="20" y2="129.6"/><line x1="2" y1="145.3" x2="20" y2="145.3"/><line x1="2" y1="161" x2="20" y2="161"/><line x1="2" y1="176.7" x2="20" y2="176.7"/><line x1="2" y1="192.4" x2="20" y2="192.4"/><line x1="2" y1="208.1" x2="20" y2="208.1"/><line x1="2" y1="223.8" x2="20" y2="223.8"/><line x1="2" y1="239.5" x2="20" y2="239.5"/><line x1="2" y1="255.2" x2="20" y2="255.2"/>
  </g>
</svg>

<!-- Notebook spread -->
<section class="piece notebook-open" aria-label="Notebook inner pages">
  <div class="page">
    <div class="mark"><span class="dot"></span>Bluecrest Learning Corps</div>
    <div class="date">Date......./....../.......</div>
    <div class="lines"></div>
  </div>
  <div class="page">
    <div class="mark"><span class="dot"></span>Bluecrest Learning Corps</div>
    <div class="date">Date......./....../.......</div>
    <div class="lines"></div>
  </div>
</section>
<svg class="rings" viewBox="0 0 14 262" aria-hidden="true">
  <g stroke="#333" stroke-width="2" stroke-linecap="round">
    <line x1="1" y1="5" x2="13" y2="5"/><line x1="1" y1="16" x2="13" y2="16"/><line x1="1" y1="27" x2="13" y2="27"/><line x1="1" y1="38" x2="13" y2="38"/><line x1="1" y1="49" x2="13" y2="49"/><line x1="1" y1="60" x2="13" y2="60"/><line x1="1" y1="71" x2="13" y2="71"/><line x1="1" y1="82" x2="13" y2="82"/><line x1="1" y1="93" x2="13" y2="93"/><line x1="1" y1="104" x2="13" y2="104"/><line x1="1" y1="115" x2="13" y2="115"/><line x1="1" y1="126" x2="13" y2="126"/><line x1="1" y1="137" x2="13" y2="137"/><line x1="1" y1="148" x2="13" y2="148"/><line x1="1" y1="159" x2="13" y2="159"/><line x1="1" y1="170" x2="13" y2="170"/><line x1="1" y1="181" x2="13" y2="181"/><line x1="1" y1="192" x2="13" y2="192"/><line x1="1" y1="203" x2="13" y2="203"/><line x1="1" y1="214" x2="13" y2="214"/><line x1="1" y1="225" x2="13" y2="225"/><line x1="1" y1="236" x2="13" y2="236"/><line x1="1" y1="247" x2="13" y2="247"/><line x1="1" y1="258" x2="13" y2="258"/>
  </g>
</svg>

<!-- Brochure, opened flat -->
<section class="piece brochure" aria-label="Brochure cover spread">
  <div class="panel back">
    <div class="mark"><span class="dot"></span>Bluecrest Learning Corps</div>
    <div class="addr">
      4719 Pellham Court, Harlow Ridge, VA 22471<br>
      <svg class="ico" viewBox="0 0 10 10"><path d="M1 3c0-1 1-2 2-2h4c1 0 2 1 2 2v1H7V3H3v1H1zM2 5h6l1 4H1z"/></svg>(703) 482-1736&nbsp;&nbsp;
      <svg class="ico" viewBox="0 0 10 10"><path d="M1 3c0-1 1-2 2-2h4c1 0 2 1 2 2v1H7V3H3v1H1zM2 5h6l1 4H1z"/></svg>(301) 647-2208
    </div>
  </div>
  <div class="panel front">
    <div class="mark on-gold"><span class="dot"></span>Bluecrest Learning Corps</div>
    <div class="credit">Dr. Venrel T Oskamp, CEO / Marisa Deltoft, Respresentative</div>
  </div>
</section>

<!-- Presentation folder, opened flat -->
<section class="piece folder" aria-label="Presentation folder interior">
  <div class="panel">
    <div class="pocket pocket-gold">
      <div class="mark on-gold"><span class="dot"></span>Bluecrest Learning Corps</div>
    </div>
  </div>
  <div class="panel">
    <div class="pocket pocket-navy"></div>
    <div class="mini-card">
      <span class="dot"></span>
      <div class="info">
        <div class="name">Dr. Venrel T Oskamp</div>
        CEO<br>4719 Pellham Court,<br>Harlow Ridge, VA 22471<br>(703) 482-1736
      </div>
    </div>
  </div>
</section>

</body>
</html>
```